Business Card Design

I need a logo and a business card design that can be used for my business stationary, Facebook page and in the future a website. I don't know if I need a large design for brochures and stationery and a small portion of that as the logo or business card design. I probably need some advice about that. My new company is called Willowbank Family Circle. I don't have all of my business contact details available yet, but I want to get the design ready, so that when all this information is available I can get the printing done quickly.I'm a social worker and my business will be providing parenting groups and counselling sessions for parents.I would like the logo and business card to be very feminine and pretty. I want a silhouette image of a Mother and Baby and decorative swirls of flowers/vines/leaves and butterflies.I have found some designs elsewhere that are along the lines of what I am looking for. These images are attached below, but the quality of these attachments is very poor as I photographed them with my phone.My preferred colours would be to use black and white, purple and/or pink, aqua and or blue/green.There are four logo/business card options attached. Logo option 1 - I really like the flower and vine design. Logo option 2 - again I like the flowers and leaf design and the use of colour and the silhouette image of the Mum and Baby; Logo option 3 - I like the butterflies and decorative swirls in this option and Logo option 4 - I think this design is the best for a logo. I love the mother and baby image. I don't like the tree branch and the birds but I like the way the hair has been incorporated into the branch. I prefer the design of the flowers/vine/leaves in the other options.

Industry/Entity Type

Business

Contact Information for Business Card

Company Name:Embrace Attachment ParentingMobile:0417 751 394Email:Currently sourcing - TBAContact Name:Janelle ApplegarthQualifications:Currently sourcing details - TBA

Font styles to use
Script

Colors
33a6d7
85cae6
886aae
6c459b
e667a6
eea4c8

Requirements
Must have
• My project must have an image of a mother and child, slightly encircled by the mother's hair perhaps in a heart shape, and the mother's hair becoming a beautiful filigree design of vine/leaves/flowers and with some butterfly somewhere.
• Can all of the Words be in the same font Attachment Parenting can be slightly smaller.
Nice to have
• I would like to also have a similar vine/leaves/flowers and maybe a butterfly on the opposite side of the card. Maybe the Mother/child image on the top left of the card and the other pattern on the bottom right.
• If possible the use of aqua, purple and pink.

```html
<!DOCTYPE html>
<html lang="en">
<head>
<meta charset="utf-8">
<title>Willowbank Family Circle – Business Card</title>
<link rel="stylesheet" href="https://fonts.googleapis.com/css2?family=Open+Sans:wght@400;600&display=swap">
<style>
  :root {
    --teal-deep: #137380;
    --teal-bright: #139ea8;
    --teal-wash: #d3e6ea;
    --ink: #3a3a3a;
    --paper: #ffffff;
    --charcoal: #3a3a3a;
  }
  html, body {
    margin: 0;
    padding: 0;
    overflow: hidden;
    background: var(--paper);
  }
  .card {
    position: relative;
    width: 1200px;
    height: 686px;
    box-sizing: border-box;
    border: 2px solid var(--teal-bright);
    background: var(--paper);
    overflow: hidden;
    font-family: "Open Sans", Arial, sans-serif;
  }
  .brand-wash {
    position: absolute;
    left: 690px;
    top: 140px;
    width: 490px;
    height: 480px;
    border-radius: 50%;
    background: radial-gradient(ellipse at center, rgba(211,230,234,0.55) 0%, rgba(211,230,234,0.25) 55%, rgba(255,255,255,0) 75%);
  }
  .brand {
    position: absolute;
    left: 20px;
    top: 30px;
    width: 640px;
    text-align: center;
  }
  .brand-dot {
    display: block;
    width: 170px;
    height: 170px;
    margin: 10px auto 30px;
    border-radius: 50%;
    background: var(--teal-deep);
  }
  .brand-name {
    margin: 0;
    font-weight: 600;
    font-size: 56px;
    line-height: 1.12;
    color: var(--teal-deep);
  }
  .brand-rule {
    position: absolute;
    left: 0;
    top: 416px;
    width: 675px;
    height: 10px;
    background: var(--teal-bright);
  }
  .contact {
    position: absolute;
    left: 34px;
    display: flex;
    align-items: center;
    gap: 0;
    font-size: 28px;
    color: var(--ink);
  }
  .contact svg { flex: none; }
  .contact-email { top: 458px; }
  .contact-email .contact-text { margin-left: 53px; }
  .contact-phone { top: 550px; }
  .contact-phone .contact-text { margin-left: 93px; }
  .holder {
    position: absolute;
    left: 700px;
    top: 345px;
    width: 460px;
    text-align: center;
  }
  .holder-name {
    margin: 0;
    font-weight: 400;
    font-size: 47px;
    line-height: 1.1;
    color: var(--ink);
    white-space: nowrap;
  }
  .holder-role {
    margin: 4px 0 0;
    font-size: 23px;
    color: var(--teal-deep);
    letter-spacing: 0.5px;
  }
  .footer-band {
    position: absolute;
    left: 0;
    bottom: 0;
  }
</style>
</head>
<body>
<main class="card">
  <div class="brand-wash" role="img" aria-label="Faint decorative brand wash in pale aqua"></div>

  <header class="brand">
    <span class="brand-dot" aria-hidden="true"></span>
    <h1 class="brand-name">Willowbank<br>Family Circle</h1>
  </header>

  <div class="brand-rule"></div>

  <div class="contact contact-email">
    <svg width="50" height="36" viewBox="0 0 50 36" aria-hidden="true">
      <rect x="0" y="0" width="50" height="36" fill="var(--teal-bright)"/>
      <polyline points="0,2 25,22 50,2" fill="none" stroke="#ffffff" stroke-width="2.5"/>
      <line x1="0" y1="35" x2="18" y2="16" stroke="#ffffff" stroke-width="2"/>
      <line x1="50" y1="35" x2="32" y2="16" stroke="#ffffff" stroke-width="2"/>
    </svg>
    <span class="contact-text">Curreently Sourcing</span>
  </div>

  <div class="contact contact-phone">
    <svg width="46" height="46" viewBox="0 0 24 24" aria-hidden="true">
      <path fill="var(--teal-bright)" d="M6.6 10.8c1.4 2.8 3.8 5.1 6.6 6.6l2.2-2.2c.3-.3.7-.4 1-.2 1.1.4 2.3.6 3.6.6.6 0 1 .4 1 1V20c0 .6-.4 1-1 1C10.6 21 3 13.4 3 4c0-.6.4-1 1-1h3.5c.6 0 1 .4 1 1 0 1.3.2 2.5.6 3.6.1.3 0 .7-.2 1L6.6 10.8z"/>
    </svg>
    <span class="contact-text">0438 260 517</span>
  </div>

  <section class="holder">
    <h2 class="holder-name">Rosalind Thackeray</h2>
    <p class="holder-role">(DIRECTOR)</p>
  </section>

  <svg class="footer-band" width="1200" height="48" viewBox="0 0 1200 48" aria-hidden="true">
    <polygon points="0,0 895,0 873,48 0,48" fill="var(--teal-deep)"/>
    <polygon points="916,0 1200,0 1200,48 890,48" fill="var(--charcoal)"/>
  </svg>
</main>
</body>
</html>
```